Calder Aviation website

We are an aviation company based in Harbor Point but with worldwide coverage. We are involved in commercial aircraft (mostly freighters) trading, sale & leasing. Specifically, we specialized in freighters of the Veltram family (V316, V328, V335, V342, V359). We also assist with financing, sale/leaseback. Handle special aviation projects and provide consultancy services. Currently engaged in a Veltram 359 passenger to Freighter conversion (P2F).

Website Preliminary Initial Content/Sections as follows:

About Us
Founded in 2011, Calder Aviation's management has many years of experience in Aviation, a strong background in scheduled airlines with emphasis in all cargo operations, freight forwarding supply chain and freight logistics, as well as ACMI and CMI operations.

Calder’s focuses in facilitating wet and dry lease operations, charter and ACMI programs consultancy, aircraft sales, leasing and procurement, aviation consultancy and aircraft management.

Calder team is a hands-on reliable alternative that works toward achieving your aircraft and aviation objectives by meeting your requirements and timeframe throughout professional and personalized service.

Tiberio Salcedo has over three decades of experience in the aviation field including aircraft maintenance, airline management, supply chain and logistics management. Tiberio is a true entrepreneur with proven experience and expertise on the multiple facets of the commercial aviation industry throughout the creation and development of a cluster of aviation entities. Tiberio is the founder and former sole member/chairman of 64 Air, a Veltram 342 All-Cargo U.S. Certificated Air Carrier created from scratch in 2014 which nowadays conforms a superb growing airline platform with an immaculate compliance operational record.

Services

Aircraft Finance, Trading, Procurement and Leasing
Calder buys, sells, leases and facilitates aircraft trading while specializes in structured aircraft investment projects. Calder has deep industry relationships and years of expertise, allowing to successfully execute lease transactions. We assist airlines, financial institutions and leasing companies when selling or purchasing aircraft.

Aircraft Available for Sale/Lease

Sale/Leaseback
Sale-leaseback is a method of financing. If your company needs liquidity, your aircraft or engine can serve as collateral for a loan throughout a sale-leaseback transaction. Sale-leaseback can free the equity tied up in aircraft or asset. Even if there is no pressing need for funds, a sale-leaseback allows you to use the equity tied up in your aircraft in a more productive fashion. Leaseback arrangements are usually employed because they confer financing, accounting or taxation benefits.

Passenger to Freighter Conversion (P2F)
Pandemic has seen the resurgence of operators packing freight into the main cabins of passenger aircraft. Carriers have been allowed to transport cargo in the cabin by removing passenger seats completely. NAB/CARO have established exemptions that allow operators to fly in “Preighter” configuration for a limited time. Calder is closely working with a U.S. group that is developing a Class E Supplemental Type Certificate (STC) for applicability on V359 aircraft which will include a cargo door for containerized freight. Final approvals are expected during first quarter of 2022.
Wet lease
Throughout our deep relationships within the industry, Calder facilitates short or long-term wet leases to airlines and qualified parties around the globe, whereby we provide the Aircraft, Crews, Maintenance and Insurance (ACMI) worldwide services at competitive rates. We also specialize in AM leases where the aircraft is registered onto Lessee´s AOC with all maintenance services included in the rates, covering all maintenance risks, or CM or CMI where the client provides the aircraft.

Dry Lease
We offer aircraft from our own portfolio on dry lease or could engage in procuring the aircraft of your choice.

Asset & Aircraft Management
We provide aircraft owners Aircraft Management services, where we manage the technical side of the aircraft or the asset. Calder also provides Harlow Dynamics engines trading, repair and full management services. We also buy Veltram/Skylane surplus inventory.

Worldwide Charters
We facilitate the arrangement of full charters to airlines and logistics companies. Certain territory restrictions may apply.

Aviation Consultancy
We provide airline consultancy services for new or special projects. Calder also specializes on All Cargo International route analysis, implementation and development. Our team provides professional guidance in obtaining worldwide both scheduled and charter authority.

Target Market(s)

Our target market are the airlines, logistics companies and commercial aviation related entities

Industry/Entity Type

Commercial Aviation

Coding

Coded - Design and coding required

Number of Pages Required

3 page

Requirements
Must have
• Illustrations of wide body freighters such V359, V342, V328

```html
<!DOCTYPE html>
<html lang="en">
<head>
<meta charset="utf-8">
<title>Calder Aviation — Website Design</title>
<link href="https://fonts.googleapis.com/css2?family=Raleway:wght@400;500;600;700&family=Tenor+Sans&display=swap" rel="stylesheet">
<style>
:root{
  --navy:#001c3b;
  --mist:#bdc8ce;
  --snow:#f7f7f7;
  --canvas:#dcdfe7;
  --slate:#94a5bd;
  --text:#3a4556;
  --white:#ffffff;
}
*{box-sizing:border-box;margin:0;padding:0}
html,body{width:1200px;height:3735px;overflow:hidden}
body{background:var(--canvas);font-family:'Raleway',sans-serif;color:var(--text);position:relative}
.abs{position:absolute}

/* style guide */
.brand-mark{left:283px;top:181px;width:175px;text-align:center;font-family:'Tenor Sans',sans-serif;color:var(--navy);font-size:22px;letter-spacing:1px;line-height:1}
.brand-mark small{display:block;font-size:22px;letter-spacing:1px;margin-top:6px}
.guide-rule{width:1px;background:#9aa3b5}
.guide-title{font-family:'Raleway',sans-serif;font-size:22px;color:var(--navy);font-weight:500}
.guide-font{font-size:16px;color:#6b7486}
.swatch{width:36px;height:36px;border-radius:50%}
.swatch-label{font-size:8px;color:#6b7486;width:50px;text-align:center}

/* header + hero, reused in screens */
.site-head{width:586px;height:378px;position:relative;overflow:hidden;background:var(--white)}
.topbar{height:19px;background:var(--mist);display:flex;align-items:center;padding:0 115px;font-size:5px;color:var(--navy);gap:14px}
.topbar .social{margin-left:auto;display:flex;gap:3px}
.dot{width:7px;height:7px;border-radius:50%;background:var(--navy);display:inline-block}
.navbar{height:42px;background:var(--navy);display:flex;align-items:center;padding:0 115px}
.logo{font-family:'Tenor Sans',sans-serif;color:var(--white);font-size:9px;letter-spacing:1px}
.menu{margin-left:auto;display:flex;gap:14px;align-items:center;font-size:5px;color:var(--white);letter-spacing:.3px}
.menu .cta{background:var(--slate);padding:6px 9px}
.hero{position:absolute;left:0;top:61px;width:586px;height:317px;background:linear-gradient(135deg,#c9d2e2 0%,#7f91b3 45%,#34487a 100%)}
.hero-card{position:absolute;left:116px;top:55px;width:356px;height:262px;background:rgba(43,57,105,.62);text-align:center;color:var(--white);padding-top:72px}
.hero-card h1{font-family:'Raleway',sans-serif;font-weight:500;font-size:21px;line-height:26px;letter-spacing:.3px}
.hero-card p{font-size:6.4px;line-height:12px;width:320px;margin:10px auto 0}

.screen{position:absolute;overflow:hidden;background:var(--white)}
.screen .site-head{transform-origin:0 0}

/* page */
.page{left:307px;top:890px;width:586px;height:2751px;background:var(--white)}
.tagline{position:absolute;left:112px;top:378px;width:474px;height:67px;background:var(--mist);display:flex;align-items:center;justify-content:center;font-size:8px;color:var(--navy)}
.eyebrow{font-size:4.5px;letter-spacing:1px;color:#8d97a8;text-transform:uppercase}
.sec-title{font-family:'Raleway',sans-serif;font-size:15px;color:var(--navy);font-weight:500}
.body-s{font-size:5px;line-height:9.5px}

.about-text{left:114px;top:533px;width:114px}
.btn{background:var(--slate);color:var(--white);font-size:4.5px;display:flex;align-items:center;justify-content:center;letter-spacing:.3px}
.play{width:22px;height:22px;border-radius:50%;background:var(--navy)}
.photo{background:linear-gradient(160deg,#dfe5ee,#8e9db8 60%,#56678c)}
.quote{left:358px;top:483px;width:114px;height:159px;background:var(--navy);color:var(--white);padding:26px 12px}
.quote .mark{font-family:'Tenor Sans',sans-serif;font-size:22px;line-height:16px}

.services{left:0;top:679px;width:586px;height:830px;background:var(--mist)}
.svc-box{background:var(--navy);color:var(--white);padding:22px 25px 0}
.svc-box h3{font-family:'Raleway',sans-serif;font-weight:500;font-size:11px;line-height:12px;margin-bottom:12px}
.svc-box p{font-size:4.6px;line-height:10px}

.brand-band{left:0;top:1509px;width:586px;height:228px;background:var(--navy)}
.brand-word{position:absolute;left:0;width:586px;top:96px;text-align:center;font-family:'Tenor Sans',sans-serif;font-size:24px;letter-spacing:17px;color:#7b8bab}

.faq-q{position:absolute;height:18px;background:var(--navy);color:var(--white);font-size:4.6px;display:flex;align-items:center;justify-content:space-between;padding:0 7px}
.faq-q span:last-child{font-size:8px}
.faq-a{position:absolute;font-size:4.4px;line-height:8px;padding:0 7px}

.leasing{left:0;top:2009px;width:586px;height:236px;background:linear-gradient(180deg,#cfd6e2 0%,#9fb0c8 45%,#8ba0bd 100%)}
.stats{left:0;top:2245px;width:586px;height:113px;background:var(--navy);color:var(--white)}
.stat{position:absolute;width:90px;text-align:center}
.stat b{display:block;font-family:'Raleway',sans-serif;font-weight:400;font-size:16px}
.stat span{font-size:4.3px;display:block;margin-top:4px}

.footer{left:0;top:2586px;width:586px;height:148px;background:var(--mist)}
.footer h4{font-family:'Raleway',sans-serif;font-size:9px;font-weight:500;color:var(--navy)}
.footer li{list-style:none;font-size:4.4px;line-height:15px;color:var(--text)}
.bottom-bar{left:0;top:2734px;width:586px;height:17px;background:var(--navy);color:#b9c3d3;font-size:4px;display:flex;align-items:center;justify-content:center}
</style>
</head>
<body>

<!-- style guide -->
<div class="abs brand-mark">CALDER<small>AVIATION</small></div>
<div class="abs guide-rule" style="left:517px;top:162px;height:81px"></div>
<div class="abs guide-title" style="left:577px;top:158px">Fonts:</div>
<div class="abs guide-font" style="left:577px;top:203px;font-family:'Tenor Sans',sans-serif">Tenor Sans</div>
<div class="abs guide-font" style="left:577px;top:226px">Raleway</div>
<div class="abs guide-rule" style="left:730px;top:162px;height:81px"></div>
<div class="abs guide-title" style="left:788px;top:158px">Colors:</div>
<div class="abs swatch" style="left:790px;top:194px;background:var(--navy)"></div>
<div class="abs swatch" style="left:838px;top:194px;background:var(--mist)"></div>
<div class="abs swatch" style="left:883px;top:194px;background:var(--snow)"></div>
<div class="abs swatch-label" style="left:783px;top:238px">#001c3b</div>
<div class="abs swatch-label" style="left:831px;top:238px">#bdc8ce</div>
<div class="abs swatch-label" style="left:876px;top:238px">#f7f7f7</div>

<!-- desktop screen -->
<div class="screen" style="left:469px;top:345px;width:586px;height:332px">
  <div class="site-head">
    <div class="topbar"><span>+1 305 555 0142</span><span>hello@calderaviation.com</span><span class="social"><i class="dot"></i><i class="dot"></i><i class="dot"></i></span></div>
    <div class="navbar"><span class="logo">CALDER AVIATION</span><nav class="menu"><span>HOME</span><span>ABOUT US</span><span>SERVICES</span><span>CONTACT</span><span class="cta">CALL US NOW</span></nav></div>
    <div class="hero" role="img" aria-label="Wide body freighter on the apron under a cloudy sky"></div>
    <div class="hero-card"><h1>WELCOME TO<br>CALDER AVIATION</h1><p>We are an aviation company based in Harbor Point but with worldwide coverage. We are involved in commercial aircraft (mostly freighters) trading, sale &amp; leasing. Specifically, we specialized in freighters of the Veltram family (V316, V328, V335, V342, V359).</p></div>
  </div>
</div>

<!-- laptop screen -->
<div class="screen" style="left:159px;top:562px;width:383px;height:231px">
  <div class="site-head" style="transform:scale(.654)">
    <div class="topbar"><span>+1 305 555 0142</span><span>hello@calderaviation.com</span><span class="social"><i class="dot"></i><i class="dot"></i><i class="dot"></i></span></div>
    <div class="navbar"><span class="logo">CALDER AVIATION</span><nav class="menu"><span>HOME</span><span>ABOUT US</span><span>SERVICES</span><span>CONTACT</span><span class="cta">CALL US NOW</span></nav></div>
    <div class="hero" role="img" aria-label="Wide body freighter on the apron under a cloudy sky"></div>
    <div class="hero-card"><h1>WELCOME TO<br>CALDER AVIATION</h1><p>We are an aviation company based in Harbor Point but with worldwide coverage. We are involved in commercial aircraft (mostly freighters) trading, sale &amp; leasing. Specifically, we specialized in freighters of the Veltram family (V316, V328, V335, V342, V359).</p></div>
  </div>
</div>

<!-- full page -->
<main class="abs page">
  <div class="site-head">
    <div class="topbar"><span>+1 305 555 0142</span><span>hello@calderaviation.com</span><span class="social"><i class="dot"></i><i class="dot"></i><i class="dot"></i></span></div>
    <div class="navbar"><span class="logo">CALDER AVIATION</span><nav class="menu"><span>HOME</span><span>ABOUT US</span><span>SERVICES</span><span>CONTACT</span><span class="cta">CALL US NOW</span></nav></div>
    <div class="hero" role="img" aria-label="Wide body freighter on the apron under a cloudy sky"></div>
    <div class="hero-card"><h1>WELCOME TO<br>CALDER AVIATION</h1><p>We are an aviation company based in Harbor Point but with worldwide coverage. We are involved in commercial aircraft (mostly freighters) trading, sale &amp; leasing. Specifically, we specialized in freighters of the Veltram family (V316, V328, V335, V342, V359).</p></div>
  </div>
  <div class="tagline">Your Most Trusted and Professional Partner in the industry of Aviation</div>

  <!-- about -->
  <div class="abs eyebrow" style="left:114px;top:484px">Introduction</div>
  <h2 class="abs sec-title" style="left:114px;top:497px">About Us</h2>
  <p class="abs body-s about-text">Founded in 2011, Calder Aviation's management has many years of experience in Aviation, a strong background in scheduled airlines with emphasis in all cargo operations, freight forwarding supply chain and freight logistics, as well as ACMI and CMI operations.</p>
  <div class="abs btn" style="left:114px;top:620px;width:56px;height:19px">LEARN MORE</div>
  <div class="abs play" style="left:176px;top:619px"><svg width="22" height="22"><path d="M9 7.5l6 3.5-6 3.5z" fill="#fff"/></svg></div>
  <div class="abs photo" style="left:233px;top:483px;width:118px;height:159px" role="img" aria-label="Company executive in a suit standing at the airport"></div>
  <div class="abs quote"><div class="mark">&ldquo;</div><p class="body-s" style="margin-top:10px">Calder’s focuses in facilitating wet and dry lease operations, charter and ACMI programs consultancy, aircraft sales, leasing and procurement, aviation consultancy and aircraft management.</p></div>

  <!-- services -->
  <section class="abs services">
    <div class="abs eyebrow" style="left:0;width:586px;text-align:center;top:37px">What we offer</div>
    <h2 class="abs sec-title" style="left:0;width:586px;text-align:center;top:50px;color:#fff">Services</h2>

    <div class="abs photo" style="left:196px;top:91px;width:276px;height:213px;background:linear-gradient(150deg,#c9d4e6,#e9c98d 45%,#8b6d52)" role="img" aria-label="Freighter taking off over cargo containers, hands on a keyboard"></div>
    <div class="abs svc-box" style="left:114px;top:116px;width:179px;height:164px"><h3>Aircraft Finance</h3><p>Calder buys, sells, leases and facilitates aircraft trading while specializes in structured aircraft investment projects. Calder has deep industry relationships and years of expertise, allowing to successfully execute lease transactions. We assist airlines, financial institutions and leasing companies when selling or purchasing aircraft.</p></div>

    <div class="abs photo" style="left:114px;top:328px;width:276px;height:215px;background:linear-gradient(140deg,#e8e4df,#a9a6ae 45%,#3f5585)" role="img" aria-label="Jet engine under maintenance"></div>
    <div class="abs svc-box" style="left:293px;top:353px;width:179px;height:165px"><h3>Asset &amp; Aircraft<br>Management</h3><p>We provide aircraft owners Aircraft Management services, where we manage the technical side of the aircraft or the asset. Calder also provides Harlow Dynamics engines trading, repair and full management services. We also buy Veltram/Skylane surplus inventory.</p></div>

    <div class="abs photo" style="left:196px;top:561px;width:276px;height:203px;background:linear-gradient(150deg,#b9c6d8,#6d7f9a 50%,#2c3448)" role="img" aria-label="Engineers reviewing plans in an aircraft hangar"></div>
    <div class="abs svc-box" style="left:114px;top:586px;width:179px;height:152px"><h3>Aviation Consultancy</h3><p>We provide airline consultancy services for new or special projects. Calder also specializes on All Cargo International route analysis, implementation and development. Our team provides professional guidance in obtaining worldwide both scheduled and charter authority.</p></div>

    <div class="abs" style="left:0;width:586px;top:783px;text-align:center;font-size:4.5px;color:var(--navy)">Click Here To View All Services &#9679;</div>
  </section>

  <!-- brand band -->
  <section class="abs brand-band">
    <div class="brand-word">CALDER AVIATION</div>
    <div class="abs" style="left:150px;top:43px;width:362px;height:123px;background:radial-gradient(ellipse at 55% 50%,rgba(235,240,248,.85) 0%,rgba(150,175,210,.4) 35%,rgba(0,28,59,0) 65%)" role="img" aria-label="Wide body airliner in flight"></div>
  </section>

  <!-- faq -->
  <div class="abs eyebrow" style="left:0;width:586px;text-align:center;top:1770px">FAQ</div>
  <h2 class="abs sec-title" style="left:0;width:586px;text-align:center;top:1783px">Frequently Asked Questions</h2>

  <div class="faq-q" style="left:114px;top:1830px;width:170px"><span>Question Number One Goes Here?</span><span>&minus;</span></div>
  <p class="faq-a" style="left:114px;top:1855px;width:170px">Lorem ipsum dolor sit amet, consectetur adipiscing elit. Ut elit tellus, luctus nec ullamcorper mattis, pulvinar dapibus leo.</p>
  <div class="faq-q" style="left:114px;top:1885px;width:170px"><span>Question Number Two Goes Here?</span><span>+</span></div>
  <div class="faq-q" style="left:114px;top:1909px;width:170px"><span>Question Number Three Goes Here?</span><span>+</span></div>
  <div class="faq-q" style="left:114px;top:1932px;width:170px"><span>Question Number Four Goes Here?</span><span>+</span></div>
  <div class="faq-q" style="left:114px;top:1956px;width:170px"><span>Question Number Five Goes Here?</span><span>+</span></div>

  <div class="faq-q" style="left:301px;top:1830px;width:171px"><span>Question Number One Goes Here?</span><span>&minus;</span></div>
  <p class="faq-a" style="left:301px;top:1855px;width:171px">Lorem ipsum dolor sit amet, consectetur adipiscing elit. Ut elit tellus, luctus nec ullamcorper mattis, pulvinar dapibus leo.</p>
  <div class="faq-q" style="left:301px;top:1885px;width:171px"><span>Question Number Two Goes Here?</span><span>+</span></div>
  <div class="faq-q" style="left:301px;top:1909px;width:171px"><span>Question Number Three Goes Here?</span><span>+</span></div>
  <div class="faq-q" style="left:301px;top:1932px;width:171px"><span>Question Number Four Goes Here?</span><span>+</span></div>
  <div class="faq-q" style="left:301px;top:1956px;width:171px"><span>Question Number Five Goes Here?</span><span>+</span></div>

  <!-- aircraft leasing -->
  <section class="abs leasing">
    <svg class="abs" style="left:0;top:0" width="586" height="40"><polygon points="0,0 586,0 586,16 293,40 0,16" fill="#fff"/></svg>
    <div class="abs" style="left:114px;top:0;width:358px;height:92px;background:radial-gradient(ellipse at 50% 55%,rgba(250,251,253,.95) 0%,rgba(210,218,230,.5) 40%,rgba(159,176,200,0) 70%)" role="img" aria-label="Wide body freighter seen head-on in flight"></div>
    <h2 class="abs" style="left:0;width:586px;top:117px;text-align:center;font-family:'Raleway',sans-serif;font-weight:500;font-size:22px;letter-spacing:2px;color:#fff">AIRCRAFT LEASING</h2>
    <p class="abs" style="left:0;width:586px;top:155px;text-align:center;font-size:5px;color:#fff">We also assist with financing, sale/leaseback. Handle special aviation projects and provide consultancy services.</p>
    <div class="abs btn" style="left:262px;top:177px;width:63px;height:21px;background:var(--navy)">REQUEST QUOTE</div>
  </section>

  <!-- stats -->
  <section class="abs stats" role="img" aria-label="Statistics over a faint world map">
    <div class="stat" style="left:113px;top:33px"><b>178</b><span>Airlines we worked with</span></div>
    <div class="stat" style="left:203px;top:33px"><b>6540</b><span>Satisfied Customers</span></div>
    <div class="stat" style="left:293px;top:33px"><b>10</b><span>Years of experience</span></div>
    <div class="stat" style="left:382px;top:33px"><b>23</b><span>Team of attested professionals</span></div>
  </section>

  <!-- testimonials -->
  <div class="abs eyebrow" style="left:0;width:586px;text-align:center;top:2392px">Testimonials</div>
  <h2 class="abs sec-title" style="left:0;width:586px;text-align:center;top:2405px">What People Say</h2>
  <div class="abs" style="left:274px;top:2440px;width:38px;height:38px;border-radius:50%;background:linear-gradient(160deg,#e6d6c8,#a88a74)" role="img" aria-label="Client portrait"></div>
  <svg class="abs" style="left:115px;top:2481px" width="8" height="10"><path d="M6 1L2 5l4 4" stroke="#8d97a8" fill="none"/></svg>
  <svg class="abs" style="left:464px;top:2481px" width="8" height="10"><path d="M2 1l4 4-4 4" stroke="#8d97a8" fill="none"/></svg>
  <p class="abs" style="left:155px;top:2492px;width:276px;text-align:center;font-size:4.4px;line-height:8px">Our fleet plans moved faster with their team. Clear advice, honest pricing and a lease closed on time, exactly as promised by them.</p>
  <div class="abs" style="left:0;width:586px;top:2518px;text-align:center;font-size:5px;font-weight:700;color:var(--navy)">ELENA VARGA</div>
  <div class="abs" style="left:285px;top:2541px;display:flex;gap:4px"><i class="dot" style="width:3px;height:3px"></i><i class="dot" style="width:3px;height:3px;background:#c4cad5"></i><i class="dot" style="width:3px;height:3px;background:#c4cad5"></i></div>

  <!-- footer -->
  <footer class="abs footer">
    <h4 class="abs" style="left:114px;top:36px">About</h4>
    <p class="abs" style="left:114px;top:52px;width:160px;font-size:4.4px;line-height:8px">Calder Aviation is a trusted partner for aircraft trading, leasing, management and consultancy worldwide.</p>
    <div class="abs" style="left:114px;top:97px;display:flex;gap:3px"><i class="dot"></i><i class="dot"></i><i class="dot"></i></div>
    <h4 class="abs" style="left:297px;top:36px">Quick Links</h4>
    <ul class="abs" style="left:297px;top:50px"><li>Home</li><li>About Us</li><li>Services</li><li>Contact</li></ul>
    <h4 class="abs" style="left:404px;top:36px">Information</h4>
    <ul class="abs" style="left:404px;top:50px"><li>+1 305 555 0142</li><li>hello@calderaviation.com</li><li>Harbor Point, Suite 400</li></ul>
  </footer>
  <div class="abs bottom-bar">Copyright 2021 © Calder Aviation · All rights reserved</div>
</main>

</body>
</html>
```